High-end construction company needs a business card design

We need a modern looking business card that draws people in, is memorable and looks so good people will want to sick it on their fridges.
On the first side what is needed are:
Logo
My name - Tomasz Brelwik
Title - Managing Director
Website - www.varkelt.co.uk
Email - tomasz@varkelt.co.uk
Telephone - 020 5194 6281
Mobile - 07845139072
On the back side was is needed is a list of all the services we provide:
-Kitchen Renovations
-Bathroom Renovations
-House Renovations
-Garage Conversions
-Extensions
-Loft Conversions
-Conservatories
-Carpentry
-Tiling
-Electrical
-Plumbing & Heating
-Bricklaying
-Landscaping
-Decorating
-Plastering
We would like the colours to be the same shades as on the logo with grey or black for the words.
Target Market(s)
Anyone who needs building work done
Contact Information for Business Card
This business card is for a construction company which strives to deliver excellent service and quality.
The look and feel of the card should represent this.
Requirements
Must have
- On the first side what is needed are:
Logo
My name - Tomasz Brelwik
Title - Managing Director
Website - www.varkelt.co.uk
Email - tomasz@varkelt.co.uk
Telephone - 020 5194 6281
Mobile - 07845139072
Nice to have
- Cool looking features

```html
<!DOCTYPE html>
<html lang="en">
<head>
<meta charset="utf-8">
<title>Varkelt Construction Ltd – Business Card</title>
<link href="https://fonts.googleapis.com/css2?family=Open+Sans:wght@400;600;700&display=swap" rel="stylesheet">
<style>
  :root {
    --backdrop: #86c257;
    --kraft: #c9a47a;
    --kraft-light: #d4b189;
    --kraft-dark: #bd976c;
    --brand-green: #5cbf3a;
    --ink: #1f1f1f;
    --ink-soft: #2e2e2e;
  }
  * { box-sizing: border-box; margin: 0; padding: 0; }
  html, body {
    width: 1200px; height: 900px; overflow: hidden;
    background: var(--backdrop);
    font-family: "Open Sans", sans-serif;
    color: var(--ink);
  }
  .canvas {
    position: relative; width: 1200px; height: 900px;
  }
  .card {
    position: absolute; left: 250px;
    width: 700px; height: 400px;
    background: radial-gradient(ellipse at 30% 20%, var(--kraft-light), var(--kraft) 55%, var(--kraft-dark));
    border-radius: 4px;
    box-shadow: 0 6px 18px rgba(0,0,0,.22);
    overflow: hidden;
  }
  .card--front { top: 35px; }
  .card--back { top: 465px; }

  /* brand name block */
  .brand {
    position: absolute;
    display: flex; align-items: center; gap: 10px;
    color: var(--brand-green); font-weight: 700;
  }
  .brand__mark {
    width: 18px; height: 18px; background: var(--brand-green);
  }
  .brand__name { line-height: 1.05; text-transform: uppercase; }
  .brand__name .big { display: block; font-size: 44px; letter-spacing: 1px; }
  .brand__name .small { display: block; font-size: 15px; letter-spacing: 3.2px; }

  .card--front .brand { left: 60px; top: 140px; }
  .card--back .brand { right: 50px; bottom: 40px; }
  .card--back .brand__name .big { font-size: 36px; }
  .card--back .brand__name .small { font-size: 12px; letter-spacing: 2.6px; }

  /* divider */
  .divider {
    position: absolute; left: 345px; top: 95px;
    width: 3px; height: 210px;
    background: linear-gradient(var(--ink) 0 45%, var(--brand-green) 45% 100%);
  }

  /* contact side */
  .person { position: absolute; left: 385px; top: 80px; }
  .person__name { font-size: 32px; font-weight: 700; color: var(--ink); }
  .person__title { font-size: 19px; font-weight: 600; color: var(--ink-soft); margin-top: 2px; }
  .contacts { list-style: none; margin-top: 26px; }
  .contacts li {
    display: flex; align-items: center; gap: 16px;
    font-size: 17px; font-weight: 600; margin-bottom: 9px; color: var(--ink-soft);
  }
  .contacts svg { width: 16px; height: 16px; flex: none; }

  /* services */
  .services__title {
    position: absolute; right: 60px; top: 50px;
    font-size: 30px; font-weight: 700; letter-spacing: .5px;
  }
  .services__rule {
    position: absolute; right: 60px; top: 98px; width: 290px; height: 3px;
    background: linear-gradient(90deg, var(--brand-green) 0 30%, var(--ink) 30% 55%, var(--brand-green) 55% 100%);
  }
  .service-list {
    position: absolute; list-style: none;
    font-size: 16px; color: var(--ink-soft);
  }
  .service-list li { margin-bottom: 8px; padding-left: 20px; position: relative; }
  .service-list li::before {
    content: ""; position: absolute; left: 0; top: 8px;
    width: 7px; height: 7px; border-radius: 50%; background: var(--ink);
  }
  .service-list--one { left: 45px; top: 60px; }
  .service-list--two { left: 275px; top: 140px; }
  .service-list--three { left: 490px; top: 160px; }
</style>
</head>
<body>
<main class="canvas">

  <section class="card card--front" aria-label="Business card front">
    <div class="brand">
      <span class="brand__mark"></span>
      <span class="brand__name"><span class="big">Varkelt</span><span class="small">Construction Ltd</span></span>
    </div>
    <div class="divider"></div>
    <div class="person">
      <h1 class="person__name">Tomasz Brelwik</h1>
      <p class="person__title">Managing Director</p>
      <ul class="contacts">
        <li>
          <svg viewBox="0 0 16 16" fill="none" stroke="#1f1f1f" stroke-width="1.4"><rect x="4" y="1" width="8" height="14" rx="1.5"/><line x1="7" y1="12.5" x2="9" y2="12.5"/></svg>
          07845139072
        </li>
        <li>
          <svg viewBox="0 0 16 16" fill="#1f1f1f"><path d="M3.5 1.5l2.5 0 1 3.5-1.6 1.2a8 8 0 0 0 4.4 4.4L11 9l3.5 1v2.5c0 1-1 2-2 2A11 11 0 0 1 1.5 3.5c0-1 1-2 2-2z"/></svg>
          020 5194 6281
        </li>
        <li>
          <svg viewBox="0 0 16 16" fill="none" stroke="#1f1f1f" stroke-width="1.4"><rect x="1" y="3" width="14" height="10" rx="1"/><path d="M1 3.5l7 5.5 7-5.5"/></svg>
          tomasz@varkelt.co.uk
        </li>
        <li>
          <svg viewBox="0 0 16 16" fill="none" stroke="#1f1f1f" stroke-width="1.3"><circle cx="8" cy="8" r="6.5"/><ellipse cx="8" cy="8" rx="3" ry="6.5"/><line x1="1.5" y1="8" x2="14.5" y2="8"/></svg>
          www.varkelt.co.uk
        </li>
      </ul>
    </div>
  </section>

  <section class="card card--back" aria-label="Business card back">
    <h2 class="services__title">List of Our Services</h2>
    <div class="services__rule"></div>
    <ul class="service-list service-list--one">
      <li>Kitchen Renovations</li>
      <li>Bathroom Renovations</li>
      <li>House Renovations</li>
      <li>Garage Conversions</li>
      <li>Extensions</li>
      <li>Plastering</li>
    </ul>
    <ul class="service-list service-list--two">
      <li>Loft Conversions</li>
      <li>Conservatories</li>
      <li>Carpentry</li>
      <li>Tiling</li>
      <li>Electrical</li>
      <li>Decorating</li>
    </ul>
    <ul class="service-list service-list--three">
      <li>Landscaping</li>
      <li>Bricklaying</li>
      <li>Plumbing &amp; Heating</li>
    </ul>
    <div class="brand">
      <span class="brand__mark"></span>
      <span class="brand__name"><span class="big">Varkelt</span><span class="small">Construction Ltd</span></span>
    </div>
  </section>

</main>
</body>
</html>
```